Manufacturer of prepared Persian ready meals needs a product concept design

I need a product concept design for a new company based in the UK called 'Valdren Kitchen Ltd'.
The winner will potentially be selected to produce prototype designs for our other products.
For this project, the product will be called "Ghormeh Sabzi". This needs to be on the design to let consumers know what it is.
Whilst still in the concept stage, the aim of the company is to produce refrigerated microwaveable / oven Persian ready meal for retail supermarket consumers, and may also have an online platform for direct to consumer sales.
I have provided quite a few competitor examples of products.
I would like the product in a black or clear round bowl. It will be split into two sections (Half stew / Half rice) by the sleeve, which you are designing. I would like the food to be visible on either side of the label, so the consumer knows what they are eating.
The logo is provided within the file attachments and needs to be on prominent display on the pouch.
The mission for Valdren Kitchen Ltd brand is:
"Bringing 2,500 years of scented history to your table".
This needs to be present on the sleeve.
The product needs to represent the ethnicity of the brand throughout the design, and the same font to be used throughout.
Persian architecture was filled with a wide range of vibrant colours and has been engineered to stand the test of time, so I would like that to be incorporated into the product design (see attached examples of Persian geometry).
Alternatively Persian carpets are world renowned for their quality, so examples of this could be displayed on the packaging.
These will have to be artistically interpreted to avoid potential copyright; I am looking for individual artistic design.
It needs to represent a super quality, royalty & decadence throughout, and stand out on the shelves to the consumer above all the other competitor products.
To comply with food standards, the sleeve must have a nutritional label on display. I have attached a generic example for you to use. You may create your own representation of it.
Ghormeh Sabzi is a natural source of fibre, high in protein, gluten and dairy free, so I would like this displayed on the sleeve, as well as the the words:
- Traditionally rich in aromatic herbs, tender slow cooked lamb, red kidney beans & dried limes
- One of the oldest dishes in Persian history
You can find pictures of the food provided in the files. Note, these are not my pictures, but give you an idea of what will be provided inside.
Some designers have uploaded the same design up to 5 times, others twice. Only 18 have been uploaded, but it says 20, so I think 2 have been removed?

```html
<!DOCTYPE html>
<html lang="en">
<head>
<meta charset="utf-8">
<title>Valdren Kitchen – Ghormeh Sabzi Sleeve</title>
<link rel="stylesheet" href="https://fonts.googleapis.com/css2?family=Jost:ital,wght@0,400;0,500;0,600;1,400&display=swap">
<style>
  :root {
    --stage: #231f20;
    --sleeve: #5c2a36;
    --panel-red: #7c0b12;
    --border-red: #9a1420;
    --gold: #f6e63e;
    --white: #ffffff;
    --energy: #d8b08a;
    --fat: #a8bf8a;
    --sugars: #8cc63f;
    --salt: #f58a4b;
    --saturates: #ec3a5c;
    --tile-ink: #3b2a25;
  }
  * { box-sizing: border-box; margin: 0; padding: 0; }
  html, body { width: 1200px; height: 1147px; overflow: hidden; background: var(--stage); }
  body { font-family: "Jost", sans-serif; position: relative; }

  .sleeve {
    position: absolute; left: 413px; top: 35px;
    width: 373px; height: 1076px;
    background: var(--sleeve);
  }
  .sleeve-art { position: absolute; inset: 0; }

  .centered { position: absolute; left: 0; width: 100%; text-align: center; }

  .brand-mark {
    position: absolute; left: 151px; top: 222px;
    width: 70px; height: 70px; background: var(--gold);
  }
  .brand-name {
    top: 318px; color: var(--white); font-weight: 500;
    font-size: 25px; letter-spacing: 7px; line-height: 30px; padding-left: 7px;
  }

  .mission {
    top: 443px; color: var(--gold); font-style: italic;
    font-size: 14px; line-height: 19px;
  }
  .product-name {
    top: 500px; color: var(--gold); font-weight: 600;
    font-size: 57px; line-height: 52px;
  }
  .weight { top: 622px; color: var(--white); font-style: italic; font-size: 22px; }
  .weight small { font-size: 11px; }

  .description {
    top: 689px; color: var(--white); font-style: italic;
    font-size: 10.5px; line-height: 14px;
  }
  .heritage { top: 737px; color: var(--gold); font-style: italic; font-size: 11.5px; }
  .serving { top: 767px; color: var(--white); font-weight: 600; font-size: 9.5px; }

  .nutrition {
    position: absolute; left: 95px; top: 784px;
    display: flex; gap: 1px;
  }
  .nutrient {
    width: 36px; height: 50px; border-radius: 18px 18px 0 0;
    text-align: center; color: var(--tile-ink); font-size: 7px; line-height: 9px;
    padding-top: 5px;
  }
  .nutrient b { display: block; font-weight: 600; font-size: 7px; }
  .nutrient .level {
    display: block; margin: 1px auto; width: 26px; background: var(--white);
    border-radius: 3px; font-weight: 600; font-size: 6px; line-height: 7px;
  }
  .nutrient.energy { background: var(--energy); }
  .nutrient.fat { background: var(--fat); }
  .nutrient.sugars { background: var(--sugars); }
  .nutrient.salt { background: var(--salt); }
  .nutrient.saturates { background: var(--saturates); }

  .intake-note {
    top: 839px; color: var(--white); font-style: italic;
    font-size: 5.5px; line-height: 8px;
  }
</style>
</head>
<body>
  <div class="sleeve">
    <svg class="sleeve-art" width="373" height="1076" viewBox="0 0 373 1076">
      <rect class="lattice-border" x="14" y="114" width="345" height="854"
            fill="none" stroke="var(--border-red)" stroke-width="10"
            role="img" aria-label="Red diamond lattice border"/>
      <rect class="inner-frame" x="24" y="126" width="324" height="831"
            fill="none" stroke="var(--border-red)" stroke-width="1"/>
      <g class="corner-panels" role="img" aria-label="Persian floral corner ornaments in red, pink, blue and green">
        <rect x="24" y="126" width="324" height="156" fill="var(--panel-red)"/>
        <path d="M110,282 C110,205 170,190 186,139 C202,190 262,205 262,282 Z" fill="var(--sleeve)"/>
        <rect x="24" y="805" width="324" height="152" fill="var(--panel-red)"/>
        <path d="M110,805 C110,882 170,897 186,948 C202,897 262,882 262,805 Z" fill="var(--sleeve)"/>
      </g>
    </svg>

    <div class="brand-mark"></div>
    <p class="centered brand-name">VALDREN<br>KITCHEN</p>

    <p class="centered mission">Bringing 2,500 years of<br>scented history to your table</p>

    <h1 class="centered product-name">GHORMEH<br>SABZI</h1>
    <p class="centered weight">400<small>g</small></p>

    <p class="centered description">Traditionally rich in aromatic herbs, Tender slow cooked lamb,<br>Red kidney beans &amp; dried limes.</p>
    <p class="centered heritage">One of the oldest dishes in Persian history.</p>

    <p class="centered serving">Each serving (150g) contains</p>
    <div class="nutrition">
      <div class="nutrient energy"><b>Energy</b>1046kJ<br>250kcal<br><br><b>13%</b></div>
      <div class="nutrient fat"><b>Fat</b>3.0g<span class="level">LOW</span><b>4%</b></div>
      <div class="nutrient sugars"><b>Sugars</b>34g<span class="level">LOW</span><b>38%</b></div>
      <div class="nutrient salt"><b>Salt</b>0.9g<span class="level">HIGH</span><b>15%</b></div>
      <div class="nutrient saturates"><b>Saturates</b>1.3g<span class="level">MED</span><b>7%</b></div>
    </div>
    <p class="centered intake-note">of an adult's reference intake<br>Typical values (as sold) per 100g: 697kJ/ 167kcal</p>
  </div>
</body>
</html>
```